Simple and Clean business card design

We would like the design to be simple clean and to incorporate our colors.

We are open to your design and talent, we have the dots in our logo as we think of it as data points and we connect data points for people.

We are open to see the great creative and clean design you bring to the table

Contact Information for Business Card

please include: name, position, email, phone and website

Font styles to use
Sans Serif

Requirements
Must have
• my colors incorporated, simplicity
Nice to have
• lots of white space, simplicity
Should not have
• complexicity/ complex art

```html
<!DOCTYPE html>
<html lang="en">
<head>
<meta charset="utf-8">
<title>Sprig business card</title>
<link href="https://fonts.googleapis.com/css2?family=Work+Sans:wght@400;500;600;700&display=swap" rel="stylesheet">
<style>
  :root {
    --stage: #1c1c1e;
    --card-black: #000000;
    --paper: #ffffff;
    --ink: #000000;
    --brand-blue: #5b7ec4;
    --text-light: #ffffff;
  }
  * { margin: 0; padding: 0; box-sizing: border-box; }
  html, body {
    width: 1200px; height: 852px; overflow: hidden;
    background: var(--stage);
    font-family: "Work Sans", Arial, sans-serif;
  }
  .stage {
    position: relative; width: 1200px; height: 852px;
  }
  .card {
    position: absolute; top: 271px;
    width: 540px; height: 309px;
    border-radius: 14px; overflow: hidden;
    background: var(--card-black);
  }
  .card--front { left: 40px; }
  .card--back { left: 620px; }

  .wordmark {
    position: absolute;
    display: flex; align-items: center; gap: 12px;
    font-weight: 600; letter-spacing: -1px; line-height: 1;
  }
  .wordmark__dot {
    width: 18px; height: 18px; border-radius: 50%;
    background: var(--brand-blue);
  }
  .card--front .wordmark {
    left: 50%; top: 50%; transform: translate(-50%, -50%);
    color: var(--text-light); font-size: 72px;
  }

  .back-shape { position: absolute; inset: 0; }
  .card--back .wordmark {
    left: 265px; top: 82px;
    color: var(--ink); font-size: 58px;
  }

  .contact {
    position: absolute; left: 30px; bottom: 26px;
    color: var(--text-light); font-size: 11.5px; line-height: 1.45;
  }
  .contact__name {
    color: var(--brand-blue); font-weight: 700; font-size: 17px;
    letter-spacing: 1px; text-transform: uppercase; line-height: 1.1;
  }
  .contact__role { font-size: 12.5px; margin-bottom: 6px; }
  .contact__address { margin-bottom: 6px; }
  .contact__line { display: flex; align-items: center; gap: 7px; }
  .contact__icon { width: 10px; height: 10px; flex: none; }
</style>
</head>
<body>
<main class="stage">

  <section class="card card--front" aria-label="Card front">
    <div class="wordmark"><span class="wordmark__dot"></span>Sprig</div>
  </section>

  <section class="card card--back" aria-label="Card back">
    <svg class="back-shape" viewBox="0 0 540 309" aria-hidden="true">
      <path d="M185,0 C215,175 390,278 540,262 L540,0 Z" fill="var(--paper)"/>
      <path d="M185,0 C215,175 390,278 540,262" fill="none" stroke="var(--brand-blue)" stroke-width="4"/>
    </svg>

    <div class="wordmark"><span class="wordmark__dot"></span>Sprig</div>

    <div class="contact">
      <p class="contact__name">Daniel Harper</p>
      <p class="contact__role">Founder</p>
      <p class="contact__address">1470 Brookfield Lane<br>Ashford, TX 75021</p>
      <p class="contact__line">
        <svg class="contact__icon" viewBox="0 0 10 10" aria-hidden="true"><path d="M2,0.5 L4,2.8 L3,4 C3.6,5.4 4.6,6.4 6,7 L7.2,6 L9.5,8 L8.2,9.5 C4.5,9 1,5.5 0.5,1.8 Z" fill="var(--brand-blue)"/></svg>
        0412 583 907
      </p>
      <p class="contact__line">
        <svg class="contact__icon" viewBox="0 0 10 10" aria-hidden="true"><rect x="0.5" y="2" width="9" height="6.5" fill="none" stroke="var(--brand-blue)" stroke-width="1.1"/><path d="M0.5,2 L5,5.8 L9.5,2" fill="none" stroke="var(--brand-blue)" stroke-width="1.1"/></svg>
        hello@brightmesh.co
      </p>
      <p class="contact__line">
        <svg class="contact__icon" viewBox="0 0 10 10" aria-hidden="true"><circle cx="5" cy="5" r="4.4" fill="none" stroke="var(--brand-blue)" stroke-width="1.1"/><ellipse cx="5" cy="5" rx="2" ry="4.4" fill="none" stroke="var(--brand-blue)" stroke-width="0.9"/><path d="M0.6,5 H9.4" stroke="var(--brand-blue)" stroke-width="0.9"/></svg>
        www.brightmesh.co
      </p>
    </div>
  </section>

</main>
</body>
</html>
```